Small legal and financial translation company needs Squarespace website, brochure and logo

Hello,
We are Lumarin Services (www.lumarinservices-example.com), a boutique legal and financial translation company. We offer our services mainly to Spanish customers. Our primary line of business is the translation of financial statements, but we translate a wide variety legal and financial texts.
The project we are offering comprises three parts: a redo of the current website, an informational brochure for potential customer and a logo design. These three parts should provide a consistent image. We would develop content soon.
We are looking for a website that would look like a typical law firm website, nothing too fancy. Right now, it is in English, Spanish and French, although the new site need only be in English and Spanish. There must be good toggling between the English and Spanish versions. There would be no need for tie-ins to social media and it would not contain a blog. Basically, a static site. We aren't interesting in driving traffic to the site or SEO, as we will contact nearly all potential customers beforehand. The website must be built in Squarespace to enable a smooth transition. The content would be similar to the current page, we'll be working on the exact content, but a rough draft is attached.
The brochure will be some three pages and would introduce the company to potential customers, using similar images as the website and the logo to be designed.
The only specifications for the logo is, as the website and brochure, it convey a sense of security and trust.
Feel free to ask with any questions as this is the first time we have used this platform.
Thank you!
Updates

I've added a more or less final version for the text in the brochure and updated the brief. Added Wednesday, June 10, 2015

Target Market(s)

Spanish law firms, auditors, accountants, banks, investment firms

Industry/Entity Type

Finance

Logo Text

Lumarin Services

Number of Pages Required

5+ page

Font styles to use
Serif

Requirements
Must have
• The website must be built in Squarespace and have a good option to toggle between English and Spanish versions.
• Brochure must be in both English and Spanish, I'm attaching a rough draft of the information that it will probably have. This should give an idea about what to include and the spacing. I will update it to include the final information.
Nice to have
• Would be nice to have some quality finance- and legal-related images
Should not have
• Vibrant colours

```html
<!DOCTYPE html>
<html lang="en">
<head>
<meta charset="utf-8">
<title>Financial Translation — Lumarin Services</title>
<link rel="stylesheet" href="https://fonts.googleapis.com/css2?family=EB+Garamond:wght@400;500&family=Montserrat:wght@400;500;600;800&display=swap">
<style>
  :root {
    --page-bg: #ececec;
    --hero-dark: #2a2a2a;
    --hero-mid: #8c8c8c;
    --hero-light: #c9c9c9;
    --white: #ffffff;
    --accent-blue: #9fd9ea;
    --nav-active: #bfe6f3;
    --heading-green: #2f6a5a;
    --text-body: #4a4a4a;
    --text-muted: #a3a3a3;
    --text-active: #222222;
    --footer-top: #333333;
    --footer-bottom: #1e1e1e;
  }
  * { box-sizing: border-box; margin: 0; padding: 0; }
  html, body { width: 1200px; height: 1075px; overflow: hidden; }
  body { background: var(--page-bg); font-family: "EB Garamond", Georgia, serif; position: relative; }

  .hero {
    position: absolute; left: 0; top: 0; width: 1200px; height: 497px;
    background:
      radial-gradient(ellipse at 25% 75%, rgba(30,30,30,.55), transparent 55%),
      linear-gradient(100deg, var(--hero-dark) 0%, var(--hero-mid) 30%, var(--hero-light) 55%, var(--hero-mid) 80%, #b5b5b5 100%);
  }
  .brand {
    position: absolute; left: 22px; top: 30px; display: flex; align-items: center; gap: 10px;
    font-family: "EB Garamond", Georgia, serif; font-size: 30px; color: var(--accent-blue); letter-spacing: .5px;
  }
  .brand-mark { width: 14px; height: 14px; background: var(--accent-blue); }
  .main-nav { position: absolute; right: 20px; top: 52px; display: flex; gap: 27px; }
  .main-nav a {
    font-family: Montserrat, Arial, sans-serif; font-size: 11.5px; font-weight: 600; letter-spacing: 1.6px;
    color: var(--white); text-decoration: none;
  }
  .main-nav a.is-current { color: var(--nav-active); }
  .hero-title {
    position: absolute; left: 0; width: 1200px; top: 196px; text-align: center;
    font-family: Montserrat, Arial, sans-serif; font-weight: 800; font-size: 58px; line-height: 86px;
    letter-spacing: 4px; color: var(--white);
  }

  .content { position: absolute; top: 580px; left: 185px; width: 820px; display: flex; }
  .side-nav { width: 222px; }
  .side-nav h2 { font-weight: 400; font-size: 19px; color: var(--heading-green); margin-bottom: 8px; }
  .side-nav a {
    display: block; font-family: Montserrat, Arial, sans-serif; font-size: 11.5px; letter-spacing: 1.4px;
    color: var(--text-muted); text-decoration: none; line-height: 14px; margin-bottom: 10px;
  }
  .side-nav a.is-current { color: var(--text-active); }
  .services h1 { font-weight: 400; font-size: 25px; letter-spacing: 1.3px; color: var(--text-body); line-height: 32px; }
  .service-lists { display: flex; margin-top: 27px; margin-left: 20px; }
  .service-lists ul { list-style: none; width: 320px; }
  .service-lists li {
    position: relative; padding-left: 15px; font-size: 17px; letter-spacing: 1.4px; line-height: 23px;
    color: var(--text-body); margin-bottom: 10px;
  }
  .service-lists li::before { content: "•"; position: absolute; left: 0; }

  .footer-top { position: absolute; left: 0; top: 960px; width: 1200px; height: 55px; background: var(--footer-top); }
  .footer-bottom { position: absolute; left: 0; top: 1015px; width: 1200px; height: 60px; background: var(--footer-bottom); }
</style>
</head>
<body>
  <header class="hero" role="img" aria-label="Black and white photo of business people standing by an office window beside a laptop on a desk">
    <div class="brand"><span class="brand-mark"></span>Lumarin Services</div>
    <nav class="main-nav">
      <a href="#" class="is-current">HOME</a>
      <a href="#">ENGLISH</a>
      <a href="#">SPANISH</a>
    </nav>
    <div class="hero-title">FINANCIAL<br>TRANSLATION</div>
  </header>

  <main class="content">
    <aside class="side-nav">
      <h2>English</h2>
      <a href="#">WHO WE ARE</a>
      <a href="#">BENEFITS</a>
      <a href="#">LEGAL TRANSLATION</a>
      <a href="#" class="is-current">FINANCIAL<br>TRANSLATION</a>
      <a href="#">CONTACT</a>
    </aside>
    <section class="services">
      <h1>Financial translation includes but is not limited to:</h1>
      <div class="service-lists">
        <ul>
          <li>financial statements and notes to the financial statements</li>
          <li>annual reports</li>
          <li>auditor's reports</li>
          <li>director's reports</li>
          <li>limited reviews</li>
        </ul>
        <ul>
          <li>business plans</li>
          <li>macroeconomic reports</li>
          <li>investment fund reports</li>
          <li>annual banking reports</li>
          <li>financing agreements</li>
        </ul>
      </div>
    </section>
  </main>

  <footer>
    <div class="footer-top"></div>
    <div class="footer-bottom"></div>
  </footer>
</body>
</html>
```